Veltrano.co - Polar Expeditions Specialists

We need a modern, visually striking business card for Veltrano.co, a company specialized in selling expedition cruises to the most remote regions on Earth, with a focus on the Arctic and Antarctica. The design should instantly communicate that the cardholder is an expert in polar travel. Use clean, premium aesthetics with cool tones like icy blue and white, possibly incorporating polar imagery (ice, glaciers, penguins, etc.)

Attached the logo

Contact Information for Business Card

Feels high-end and trustworthy.. Visually memorable — encourages people to keep it

Colors
0054AA
0677BA
7BADD7
CADEEF
E8F1F8

Requirements
Must have
• ice, glaciers, penguins, montains
Nice to have
• modern, transparente,

```html
<!DOCTYPE html>
<html lang="en">
<head>
<meta charset="utf-8">
<title>Veltrano.co – Business Card</title>
<link rel="stylesheet" href="https://fonts.googleapis.com/css2?family=Montserrat:wght@400;700&family=Poppins:wght@600;700&display=swap">
<style>
  :root {
    --brand-blue: #2C72B5;
    --deep-blue: #0054AA;
    --mid-blue: #0677BA;
    --soft-blue: #7BADD7;
    --pale-blue: #CADEEF;
    --ice: #E8F1F8;
    --white: #FFFFFF;
    --ink: #3A3A3A;
    --backdrop: #EEEFF1;
  }
  * { margin: 0; padding: 0; box-sizing: border-box; }
  html, body { width: 1192px; height: 1200px; overflow: hidden; }
  body { background: var(--backdrop); position: relative; font-family: "Montserrat", sans-serif; }

  .card {
    position: absolute; left: 219px; width: 754px; height: 432px;
    border-radius: 43px; overflow: hidden;
    box-shadow: 0 14px 30px rgba(0,0,0,0.18);
  }
  .card--front { top: 145px; background: var(--white); }
  .card--back { top: 622px; }

  /* front */
  .brand { position: absolute; left: 40px; top: 72px; display: flex; align-items: center; gap: 18px; }
  .brand__dot { width: 70px; height: 70px; border-radius: 50%; background: var(--brand-blue); }
  .brand__name { font-family: "Poppins", sans-serif; font-weight: 700; font-size: 46px; line-height: 1; color: var(--brand-blue); letter-spacing: -0.5px; }
  .brand__tagline { font-family: "Poppins", sans-serif; font-weight: 600; font-size: 13.5px; color: var(--brand-blue); margin-top: 6px; }

  .front-art {
    position: absolute; left: 452px; top: 60px; width: 218px; height: 228px;
    background: linear-gradient(180deg, rgba(232,241,248,0.4), var(--ice));
    border-radius: 110px 110px 0 0;
  }

  .holder { position: absolute; left: 40px; top: 208px; }
  .holder__name { font-weight: 700; font-size: 29px; color: var(--brand-blue); letter-spacing: 0.5px; line-height: 1.05; }
  .holder__role { font-size: 19px; color: var(--ink); line-height: 1.3; }

  .divider { position: absolute; left: 40px; top: 288px; width: 675px; height: 1.5px; background: var(--brand-blue); }

  .contacts { position: absolute; left: 40px; top: 309px; list-style: none; }
  .contacts li { display: flex; align-items: center; gap: 8px; font-size: 17.5px; color: var(--ink); height: 30.5px; }
  .contacts svg { width: 13px; height: 13px; fill: var(--brand-blue); }

  .address { position: absolute; right: 39px; top: 345px; text-align: right; font-size: 17.5px; color: var(--ink); line-height: 24.5px; }

  .accent-bar { position: absolute; left: 457px; bottom: 0; width: 258px; height: 15px; background: var(--brand-blue); }

  /* back */
  .back-photo { position: absolute; inset: 0; background: radial-gradient(ellipse at 52% 55%, #7FAAD6 0%, #5A91C8 45%, #4D87C1 100%); }
  .back-brand { position: absolute; left: 132px; top: 160px; display: flex; align-items: center; gap: 24px; }
  .back-brand__dot { width: 110px; height: 110px; border-radius: 50%; background: var(--white); }
  .back-brand__name { font-family: "Poppins", sans-serif; font-weight: 700; font-size: 66px; line-height: 1; color: var(--white); letter-spacing: -0.5px; }
  .back-brand__tagline { font-family: "Poppins", sans-serif; font-weight: 600; font-size: 20px; color: var(--white); margin-top: 10px; }
</style>
</head>
<body>

<section class="card card--front">
  <div class="brand">
    <span class="brand__dot"></span>
    <div>
      <div class="brand__name">Veltrano.co</div>
      <div class="brand__tagline">Polar Expeditions Specialists</div>
    </div>
  </div>

  <div class="front-art" role="img" aria-label="Faint pale-blue brand decoration"></div>

  <div class="holder">
    <div class="holder__name">MARTIN SOLBERG</div>
    <div class="holder__role">CEO / Founder</div>
  </div>

  <div class="divider"></div>

  <ul class="contacts">
    <li><svg viewBox="0 0 16 16"><path d="M1 6c0-2 3-3 7-3s7 1 7 3v1h-3V6H4v1H1zM4 8h8l2 6H2z"/></svg>+43 660 21 87 395</li>
    <li><svg viewBox="0 0 16 16"><path d="M1 4h14v9H1zM2 5l6 5 6-5v-.5H2z"/></svg>martin.solberg@veltrano.co</li>
    <li><svg viewBox="0 0 16 16"><circle cx="8" cy="8" r="7"/></svg>www.veltrano.co</li>
  </ul>

  <div class="address">
    P.O. Box 3190 Harbour Road<br>
    Norland NV 4821
  </div>

  <div class="accent-bar"></div>
</section>

<section class="card card--back">
  <div class="back-photo" role="img" aria-label="Photo of a polar bear walking on snow, tinted icy blue"></div>
  <div class="back-brand">
    <span class="back-brand__dot"></span>
    <div>
      <div class="back-brand__name">Veltrano.co</div>
      <div class="back-brand__tagline">Polar Expeditions Specialists</div>
    </div>
  </div>
</section>

</body>
</html>
```